Business Cards

Need business card design that I can update for new employees and details. Needs to incorporate our logo, be bright and fun (in line with tourism and holidays)
Would like a Map of Western Australia on the front with locations all the caravan parks we own (just purchased Tom Price so please include that as well as others listed on our website).
Target Market(s)
Famillies
Contact Information for Business Card
5 Cards -
Neil Perrow (Director) e: perrow@wattlebay.com.au p: 0491 570 156
Mira Perrow (Director) e: perrow@wattlebay.com.au p: 0491 570 157
Owen Halvey (General Manager) e: halvey@wattlebay.com.au p: 0491 570 158
Helen Halvey (General Manager) e: halvey@wattlebay.com.au p: 0491 570 159
Colin Danby (Training and Operations Manager) - e: danby@wattlebay.com.au p:0491 570 110
Colors
Look and feel

```html
<!DOCTYPE html>
<html lang="en">
<head>
<meta charset="utf-8">
<title>Wattle Bay Tourist Parks – Business Card</title>
<link rel="stylesheet" href="https://fonts.googleapis.com/css2?family=Cinzel:wght@400&family=Libre+Baskerville:ital,wght@1,700&family=Open+Sans:wght@400&display=swap">
<style>
  :root {
    --backdrop: #1b1b1b;
    --card-back: #6bbbb0;
    --cyan: #43c1cc;
    --ink: #000000;
    --paper: #ffffff;
    --card-w: 600px;
    --card-h: 343px;
  }
  * { box-sizing: border-box; margin: 0; padding: 0; }
  html, body {
    width: 1200px;
    height: 1001px;
    overflow: hidden;
    background: var(--backdrop);
  }
  .sheet {
    position: relative;
    width: 1200px;
    height: 1001px;
  }
  .card {
    position: absolute;
    left: 300px;
    width: var(--card-w);
    height: var(--card-h);
    overflow: hidden;
  }
  .card--back {
    top: 110px;
    background: var(--card-back);
    display: flex;
    align-items: center;
    justify-content: center;
    gap: 12px;
  }
  .card--front {
    top: 520px;
    background: var(--cyan);
  }
  .card__shapes {
    position: absolute;
    inset: 0;
    width: 100%;
    height: 100%;
  }
  .brand-mark {
    width: 22px;
    height: 22px;
    border: 2px solid var(--paper);
  }
  .brand-name {
    font-family: "Cinzel", serif;
    font-weight: 400;
    color: var(--paper);
    letter-spacing: 0.12em;
    line-height: 1;
  }
  .card--back .brand-name { font-size: 30px; }
  .front-brand {
    position: absolute;
    left: 38px;
    top: 132px;
    display: flex;
    align-items: center;
    gap: 10px;
  }
  .front-brand .brand-name { font-size: 22px; }
  .front-brand .brand-mark { width: 18px; height: 18px; }
  .person {
    position: absolute;
    right: 40px;
    top: 80px;
    text-align: right;
    color: var(--paper);
  }
  .person__name {
    font-family: "Libre Baskerville", serif;
    font-style: italic;
    font-weight: 700;
    font-size: 17px;
    letter-spacing: 0.03em;
    text-transform: uppercase;
  }
  .person__role {
    font-family: "Open Sans", sans-serif;
    font-size: 15px;
    margin-top: 2px;
  }
  .contact {
    position: absolute;
    right: 40px;
    bottom: 52px;
    list-style: none;
    color: var(--paper);
    font-family: "Open Sans", sans-serif;
    font-size: 16px;
    text-align: right;
  }
  .contact__item {
    display: flex;
    justify-content: flex-end;
    align-items: center;
    gap: 10px;
    line-height: 1.35;
  }
  .contact__icon { width: 13px; height: 13px; flex: none; }
</style>
</head>
<body>
<main class="sheet">

  <section class="card card--back" aria-label="Card back">
    <span class="brand-mark" aria-hidden="true"></span>
    <span class="brand-name">Wattle Bay</span>
  </section>

  <section class="card card--front" aria-label="Card front">
    <svg class="card__shapes" viewBox="0 0 600 343" preserveAspectRatio="none" aria-hidden="true">
      <path d="M0 0 H292 C330 70 330 250 200 343 H0 Z" fill="var(--paper)"/>
      <path d="M0 0 H270 C312 80 300 270 176 343 H0 Z" fill="var(--ink)"/>
    </svg>

    <div class="front-brand">
      <span class="brand-name">Wattle Bay</span>
      <span class="brand-mark" aria-hidden="true"></span>
    </div>

    <div class="person">
      <p class="person__name">Neil Perrow</p>
      <p class="person__role">Director</p>
    </div>

    <ul class="contact">
      <li class="contact__item">
        <span>0491 570 156</span>
        <svg class="contact__icon" viewBox="0 0 16 16" aria-hidden="true"><path fill="#fff" d="M3 1.5 5.5 1l1.5 3.5-1.7 1.2a8 8 0 0 0 5 5l1.2-1.7L15 10.5 14.5 13c-.2 1-1 1.5-2 1.4C6.6 13.7 2.3 9.4 1.6 3.5 1.5 2.5 2 1.7 3 1.5Z"/></svg>
      </li>
      <li class="contact__item">
        <span>perrow@wattlebay.com.au</span>
        <svg class="contact__icon" viewBox="0 0 16 16" aria-hidden="true"><rect x="1" y="3" width="14" height="10" fill="#fff"/><path d="M1 3 8 9l7-6" fill="none" stroke="var(--cyan)" stroke-width="1.3"/></svg>
      </li>
    </ul>
  </section>

</main>
</body>
</html>
```